Business Cards for company that supports physicians that do medical research

Need to create a business card for Qorvel Studies (www.qorvelstudies.example), a company devoted to supporting physicians who conduct medical research. The form of the card should match the message of research and information quest. I have provided the logo of the company as an uploaded file. Designs should be simple and slick aimed at very high end clients.

Target Market(s)

Medical doctors that are also researchers

Industry/Entity Type

Medical

Contact Information for Business Card

Should feature logo and fields for personal info:
Name/title
Phone /email

Font styles to use
Serif
Sans Serif

Requirements
Must have
• Qorvel logo and fields for personal info:
• Name: Bertrand Okonfu
• Title: VP Research and Senior Analyst
• Phone: 555-203-4719
• email: info@qorvelstudies.example
Nice to have
• Interesting cards that I've seen:
• 1- all black/charcoal or very dark background
• 2- Plastic - semi-transparent
• 3- non-standard height-width ratios
• 4- Functional cards -- USB drive incorporated
Should not have
• Too busy; needs to stay very simple

```html
<!DOCTYPE html>
<html lang="en">
<head>
<meta charset="UTF-8">
<title>Qorvel Studies – Business Card</title>
<link href="https://fonts.googleapis.com/css2?family=Open+Sans:wght@400;600;700&display=swap" rel="stylesheet">
<style>
  :root {
    --stage: #ecebe8;
    --card-black: #000000;
    --accent-green: #5cc044;
    --brand-blue: #1f86c6;
    --logo-grey: #6d6e70;
    --white: #ffffff;
  }
  * { margin: 0; padding: 0; box-sizing: border-box; }
  html, body {
    width: 1200px; height: 900px; overflow: hidden;
    background: var(--stage);
    font-family: "Open Sans", Arial, sans-serif;
  }
  .canvas { position: relative; width: 1200px; height: 900px; }

  .card { position: absolute; overflow: hidden; box-shadow: 0 6px 18px rgba(0,0,0,0.18); }

  /* Front card */
  .card--front { left: 238px; top: 62px; width: 555px; height: 342px; background: var(--brand-blue); }
  .front__head {
    position: absolute; left: 0; top: 0; width: 100%; height: 210px;
    background: var(--card-black);
    display: flex; align-items: center; justify-content: center;
  }
  .front__rule { position: absolute; left: 0; top: 210px; width: 100%; height: 7px; background: var(--accent-green); }

  .wordmark { display: flex; align-items: center; gap: 14px; font-weight: 600; }
  .wordmark__dot { width: 18px; height: 18px; border-radius: 50%; }
  .wordmark--front { color: var(--accent-green); font-size: 46px; letter-spacing: 0.5px; }
  .wordmark--front .wordmark__dot { background: var(--brand-blue); }
  .wordmark--back { color: var(--white); font-size: 50px; letter-spacing: 0.5px; }
  .wordmark--back .wordmark__dot { background: var(--white); }

  .person {
    position: absolute; right: 291px; top: 248px; text-align: right; color: var(--white);
  }
  .person__name { font-size: 19px; font-weight: 700; line-height: 24px; }
  .person__title { font-size: 14px; font-weight: 400; line-height: 24px; }

  .contact { position: absolute; left: 303px; top: 254px; color: var(--white); font-size: 14px; }
  .contact__row { display: flex; align-items: center; gap: 10px; height: 24px; }
  .contact__icon { width: 15px; height: 15px; flex: none; }

  /* Back card */
  .card--back {
    left: 457px; top: 518px; width: 560px; height: 342px; background: var(--brand-blue);
    display: flex; align-items: center; justify-content: center;
  }
</style>
</head>
<body>
<main class="canvas">
  <section class="card card--front" aria-label="Business card front">
    <div class="front__head">
      <div class="wordmark wordmark--front"><span class="wordmark__dot"></span>Qorvel Studies</div>
    </div>
    <div class="front__rule"></div>
    <div class="person">
      <p class="person__name">Bertrand Okonfu</p>
      <p class="person__title">VP Research and Senior Analyst</p>
    </div>
    <div class="contact">
      <div class="contact__row">
        <svg class="contact__icon" viewBox="0 0 15 15" aria-hidden="true">
          <rect width="15" height="15" rx="2" fill="#fff"/>
          <path d="M3 5.2c0-1 .8-1.7 1.8-1.7h5.4c1 0 1.8.7 1.8 1.7v.6H9.4v-.9H5.6v.9H3z" fill="#1f86c6"/>
          <rect x="4" y="7" width="7" height="4.5" rx="1" fill="#1f86c6"/>
        </svg>
        <span>555-203-4719</span>
      </div>
      <div class="contact__row">
        <svg class="contact__icon" viewBox="0 0 15 15" aria-hidden="true">
          <rect width="15" height="15" rx="2" fill="#fff"/>
          <rect x="3" y="4.5" width="9" height="6.5" fill="#1f86c6"/>
          <path d="M3 4.5l4.5 3.7L12 4.5" fill="none" stroke="#fff" stroke-width="1"/>
        </svg>
        <span>info@qorvelstudies.example</span>
      </div>
    </div>
  </section>

  <section class="card card--back" aria-label="Business card back">
    <div class="wordmark wordmark--back"><span class="wordmark__dot"></span>Qorvel Studies</div>
  </section>
</main>
</body>
</html>
```